Structural Engineering Business Card

Brookvane Drafting does residential house plans for clients in Central Florida. Would like simple but elegant business card that is appropriate for a house plan engineering company. Prefer black business card with black/white them but open to other shades of blue. I uploaded a sample card that I came across that looked good but please come up with your own creative designs.

Contact Information for Business Card

Name, Title, Phone, Email, Address, website

```html
<!DOCTYPE html>
<html lang="en">
<head>
<meta charset="UTF-8">
<title>Brookvane Drafting — Business Card</title>
<link href="https://fonts.googleapis.com/css2?family=Montserrat:wght@400;500;800&display=swap" rel="stylesheet">
<style>
  :root {
    --backdrop: #cfcfcf;
    --card-white: #ffffff;
    --card-black: #050505;
    --ink: #0a0a0a;
    --ink-soft: #6b6b6b;
    --paper: #ffffff;
  }
  * { margin: 0; padding: 0; box-sizing: border-box; }
  html, body {
    width: 1200px; height: 1200px; overflow: hidden;
    background: var(--backdrop);
    font-family: "Montserrat", sans-serif;
  }
  .canvas { position: relative; width: 1200px; height: 1200px; }
  .card { position: absolute; left: 220px; width: 760px; height: 434px; overflow: hidden; }
  .card--front { top: 140px; background: var(--card-white); color: var(--ink); }
  .card--back  { top: 626px; background: var(--card-black); color: var(--paper); }

  .holder { position: absolute; left: 96px; top: 70px; }
  .holder__name {
    font-weight: 800; font-size: 27px; letter-spacing: 0.5px; text-transform: uppercase; line-height: 1;
  }
  .holder__title { font-weight: 400; font-size: 19px; color: var(--ink-soft); margin-top: 4px; }
  .rule {
    position: absolute; left: 96px; top: 150px; width: 600px; height: 3px; background: var(--ink);
  }
  .contact {
    position: absolute; left: 70px; top: 232px; font-size: 18px; font-weight: 500; line-height: 1.32;
    list-style: none;
  }
  .contact__address { margin-bottom: 6px; }
  .contact__item { display: flex; align-items: center; gap: 10px; white-space: nowrap; }
  .contact__icon { width: 15px; height: 15px; flex: none; color: var(--ink-soft); }

  .brand {
    position: absolute; display: flex; align-items: center; gap: 12px;
    font-weight: 800; text-transform: uppercase; letter-spacing: 0.5px; white-space: nowrap;
  }
  .brand__mark { display: block; flex: none; background: currentColor; }
  .card--front .brand { right: 64px; bottom: 62px; font-size: 28px; line-height: 1.05; color: var(--ink); }
  .card--front .brand__name { display: block; }
  .card--front .brand__mark { width: 22px; height: 22px; }
  .card--back .brand {
    left: 50%; top: 50%; transform: translate(-50%, -50%); font-size: 44px; color: var(--paper);
  }
  .card--back .brand__mark { width: 34px; height: 34px; }
</style>
</head>
<body>
<main class="canvas">
  <section class="card card--front">
    <div class="holder">
      <p class="holder__name">Dorian Castell</p>
      <p class="holder__title">Owner</p>
    </div>
    <div class="rule"></div>
    <ul class="contact">
      <li class="contact__address">218 Marlow Street<br>Orlando, FL 32801</li>
      <li class="contact__item">
        <svg class="contact__icon" viewBox="0 0 24 24" fill="currentColor"><path d="M6.6 10.8a15.1 15.1 0 0 0 6.6 6.6l2.2-2.2a1 1 0 0 1 1-.25 11.4 11.4 0 0 0 3.6.57 1 1 0 0 1 1 1V20a1 1 0 0 1-1 1A17 17 0 0 1 3 4a1 1 0 0 1 1-1h3.5a1 1 0 0 1 1 1c0 1.25.2 2.45.57 3.6a1 1 0 0 1-.25 1z"/></svg>
        (555) 214-0387
      </li>
      <li class="contact__item">
        <svg class="contact__icon" viewBox="0 0 24 24" fill="currentColor"><path d="M2 5h20v14H2z M2 5l10 8 10-8" stroke="#fff" stroke-width="1.6"/></svg>
        hello@brookvane.com
      </li>
      <li class="contact__item">
        <svg class="contact__icon" viewBox="0 0 24 24" fill="none" stroke="currentColor" stroke-width="2"><circle cx="12" cy="12" r="9.5"/><path d="M2.5 12h19M12 2.5c3 3 3 16 0 19M12 2.5c-3 3-3 16 0 19"/></svg>
        www.brookvane.com
      </li>
    </ul>
    <div class="brand"><span class="brand__mark"></span><span class="brand__name">Brookvane<br>Drafting</span></div>
  </section>

  <section class="card card--back">
    <div class="brand"><span class="brand__mark"></span>Brookvane Drafting</div>
  </section>
</main>
</body>
</html>
```